Business card for event manager / organizer "waiter service"

Draft of a new valuable business card for my company.
Events, personnel service providers, festivals

```html
<!DOCTYPE html>
<html lang="de">
<head>
<meta charset="utf-8">
<title>Lenz Kellnerservice – Visitenkarte</title>
<link href="https://fonts.googleapis.com/css2?family=Passion+One:wght@700&family=Jost:wght@300;400&display=swap" rel="stylesheet">
<style>
  :root {
    --bg: #dcdcdc;
    --card: #1f1c20;
    --edge: #c4571b;
    --orange: #e0691f;
    --white: #f4f4f4;
    --muted: #cfcfcf;
  }
  * { margin: 0; padding: 0; box-sizing: border-box; }
  html, body { width: 1200px; height: 800px; overflow: hidden; }
  body {
    background: var(--bg);
    display: flex;
    align-items: center;
    justify-content: center;
    gap: 40px;
    font-family: "Jost", sans-serif;
  }
  .card {
    position: relative;
    width: 520px;
    height: 336px;
    background: var(--card);
    border-radius: 20px;
    border-bottom: 3px solid var(--edge);
    overflow: hidden;
  }
  /* Contact side */
  .portrait {
    position: absolute;
    left: 0;
    bottom: 0;
    width: 230px;
    height: 250px;
    background: linear-gradient(160deg, #2a2729 0%, #0d0c0d 45%, #d9d9d9 100%);
  }
  .contact {
    position: absolute;
    top: 30px;
    right: 34px;
    text-align: right;
    color: var(--white);
  }
  .contact__name {
    font-family: "Passion One", sans-serif;
    font-weight: 700;
    font-size: 30px;
    color: var(--orange);
    letter-spacing: 1px;
    line-height: 1;
  }
  .contact__role {
    font-size: 17px;
    font-weight: 400;
    margin: 4px 0 14px;
  }
  .contact__list { list-style: none; font-size: 14.5px; font-weight: 300; line-height: 1.45; }
  .contact__list li { display: flex; align-items: center; justify-content: flex-end; gap: 8px; }
  .contact__icon { width: 12px; height: 12px; flex: none; }
  .contact__icon--blank { visibility: hidden; }
  /* Brand side */
  .brand {
    position: absolute;
    inset: 0;
    display: flex;
    align-items: center;
    justify-content: center;
    gap: 14px;
  }
  .brand__mark { width: 40px; height: 40px; background: var(--orange); flex: none; }
  .brand__text { display: flex; flex-direction: column; }
  .brand__name {
    font-family: "Passion One", sans-serif;
    font-weight: 700;
    font-size: 38px;
    color: var(--white);
    letter-spacing: 1px;
    line-height: 1;
    white-space: nowrap;
  }
  .brand__tagline {
    margin-top: 6px;
    font-size: 14px;
    font-weight: 300;
    color: var(--muted);
    white-space: nowrap;
  }
</style>
</head>
<body>
  <section class="card card--contact">
    <div class="portrait" role="img" aria-label="Foto des Inhabers als Kellner mit Tablett und Sektgläsern"></div>
    <div class="contact">
      <h1 class="contact__name">JONAS WEBERLING</h1>
      <p class="contact__role">Inhaber</p>
      <ul class="contact__list">
        <li>Birkenweg 12, 45999 Musterstadt<svg class="contact__icon contact__icon--blank" viewBox="0 0 12 12"></svg></li>
        <li>02361 555 01 23
          <svg class="contact__icon" viewBox="0 0 12 12"><path d="M3 1l2 2.5-1.2 1.3a6 6 0 0 0 3.4 3.4L8.5 7 11 9l-1.3 2C5.5 11 1 6.5 1 2.3z" fill="var(--orange)"/></svg></li>
        <li>0170 555 48 21
          <svg class="contact__icon" viewBox="0 0 12 12"><path d="M3 1l2 2.5-1.2 1.3a6 6 0 0 0 3.4 3.4L8.5 7 11 9l-1.3 2C5.5 11 1 6.5 1 2.3z" fill="var(--orange)"/></svg></li>
        <li>info@lenz-kellnerservice.de
          <svg class="contact__icon" viewBox="0 0 12 12"><rect x="0.5" y="2.5" width="11" height="7" fill="var(--orange)"/><path d="M0.5 2.5L6 6.5l5.5-4" stroke="var(--card)" fill="none"/></svg></li>
        <li>www.lenz-kellnerservice.de
          <svg class="contact__icon" viewBox="0 0 12 12"><circle cx="6" cy="6" r="5.3" fill="none" stroke="var(--orange)" stroke-width="1.2"/><path d="M0.7 6h10.6M6 0.7c-3 3-3 7.6 0 10.6M6 0.7c3 3 3 7.6 0 10.6" stroke="var(--orange)" fill="none" stroke-width="0.9"/></svg></li>
        <li>lenz-kellnerservice
          <svg class="contact__icon" viewBox="0 0 12 12"><circle cx="6" cy="6" r="5.5" fill="var(--orange)"/></svg></li>
      </ul>
    </div>
  </section>

  <section class="card card--brand">
    <div class="brand">
      <span class="brand__mark"></span>
      <div class="brand__text">
        <span class="brand__name">LENZ KELLNERSERVICE</span>
        <p class="brand__tagline">…weil jedes Fest Gastgeber verdient!</p>
      </div>
    </div>
  </section>
</body>
</html>
```